Global (re)insurance broker needs a business card design

We need a classic business card for our company that is headquartered in SG, with offices in Malaysia and Dubai. We specialise in insurance and reinsurance broking and consultancy for our global clients.

```html
<!DOCTYPE html>
<html lang="en">
<head>
<meta charset="utf-8">
<title>Vorelink Business Card</title>
<link rel="stylesheet" href="https://fonts.googleapis.com/css2?family=Montserrat:wght@700;800&family=Open+Sans:wght@400;600&display=swap">
<style>
  :root {
    --stage: #2b2b2f;
    --card: #141414;
    --blue: #2a4b9b;
    --mint: #c4dfbb;
    --ink: #f2f2f2;
  }
  * { margin: 0; padding: 0; box-sizing: border-box; }
  html, body { width: 1200px; height: 947px; overflow: hidden; }
  body {
    background: var(--stage);
    font-family: "Open Sans", Arial, sans-serif;
    display: flex;
    align-items: center;
    justify-content: center;
    gap: 24px;
  }
  .card {
    position: relative;
    width: 560px;
    height: 320px;
    background: var(--card);
    border: 2px solid var(--blue);
    border-radius: 22px;
    overflow: hidden;
  }
  .wordmark {
    font-family: "Montserrat", Arial, sans-serif;
    font-weight: 800;
    color: var(--mint);
    letter-spacing: 2px;
    line-height: 1;
  }
  .card--back { display: flex; align-items: center; justify-content: center; }
  .card--back .wordmark { font-size: 72px; }

  .card--front .wordmark { position: absolute; left: 36px; top: 40px; font-size: 46px; }
  .divider { position: absolute; inset: 0; width: 100%; height: 100%; }
  .identity { position: absolute; left: 36px; top: 132px; }
  .identity__name {
    font-family: "Montserrat", Arial, sans-serif;
    font-weight: 800;
    font-size: 22px;
    color: var(--blue);
  }
  .identity__title { font-size: 15px; color: var(--ink); margin-top: 2px; }
  .contacts { position: absolute; left: 36px; top: 200px; list-style: none; }
  .contacts li {
    display: flex; align-items: center; gap: 8px;
    font-size: 14px; color: var(--ink); line-height: 24px;
  }
  .contacts svg { width: 12px; height: 12px; fill: var(--blue); flex: none; }
  .address {
    position: absolute; right: 30px; top: 118px;
    text-align: right; font-size: 13.5px; line-height: 20px; color: var(--ink);
  }
  .band { position: absolute; left: 0; bottom: 0; width: 100%; height: 26px; }
</style>
</head>
<body>
  <section class="card card--back">
    <span class="wordmark">VORELINK</span>
  </section>

  <section class="card card--front">
    <svg class="divider" viewBox="0 0 560 320" aria-hidden="true">
      <line x1="540" y1="60" x2="210" y2="190" stroke="#2a4b9b" stroke-width="1.2"/>
    </svg>
    <span class="wordmark">VORELINK</span>
    <div class="identity">
      <p class="identity__name">Mara Quinlan</p>
      <p class="identity__title">Chief Operating Officer</p>
    </div>
    <ul class="contacts">
      <li><svg viewBox="0 0 12 12"><path d="M2.5 1l2 2.2-1 1.3a6 6 0 0 0 4 4l1.3-1 2.2 2-1.2 1.5C5 11 1 7 1 2.2z"/></svg>+65 9000 1234</li>
      <li><svg viewBox="0 0 12 12"><path d="M0 2h12v8H0zM1 3l5 3.5L11 3z"/></svg>mara@vorelink.com</li>
      <li><svg viewBox="0 0 12 12"><circle cx="6" cy="6" r="5.5"/></svg>www.vorelink.com</li>
    </ul>
    <address class="address" style="font-style:normal">
      22 Harbour Lane,<br>
      Meridian Tower #08-04,<br>
      Singapore 048000
    </address>
    <svg class="band" viewBox="0 0 560 26" preserveAspectRatio="none" aria-hidden="true">
      <polygon points="0,0 398,0 390,26 0,26" fill="#2a4b9b"/>
      <polygon points="404,0 560,0 560,26 396,26" fill="#c4dfbb"/>
    </svg>
  </section>
</body>
</html>
```